Real Estate Company / Capital Needs Cards!

need business cards designed using the logos that were just designed by pixelbarn.

Reason: per designers request deadline extended 1 day…thank you.

Target Market(s)

Investors and clients looking to purchase real estate or invest in the business.

Industry/Entity Type

Business

Requirements
Must have
• two designs - one for the real estate logo and one for the capital logo, similar but slightly different.
Nice to have
• something to make it pop (perhaps on the back)
Should not have
• much color

```html
<!DOCTYPE html>
<html lang="en">
<head>
<meta charset="utf-8">
<title>Halden Real Estate – Business Cards</title>
<link rel="stylesheet" href="https://fonts.googleapis.com/css2?family=PT+Sans:wght@400;700&display=swap">
<style>
  :root {
    --stage: #4a3122;
    --card: #050505;
    --silver-light: #f1f1ef;
    --silver-mid: #d4d4d1;
    --silver-dark: #aeaeab;
    --ink: #1c1c1c;
    --white: #ffffff;
    --logo-silver: #d8d8d6;
  }
  * { margin: 0; padding: 0; box-sizing: border-box; }
  html, body {
    width: 1200px; height: 434px; overflow: hidden;
    background: var(--stage);
    font-family: "PT Sans", sans-serif;
  }
  .stage { position: relative; width: 1200px; height: 434px; }
  .card {
    position: absolute; top: 67px;
    width: 500px; height: 300px;
    background: var(--card);
    border-radius: 28px;
    overflow: hidden;
    box-shadow: 0 10px 24px rgba(0,0,0,.45);
  }
  .card--front { left: 70px; }
  .card--back { left: 630px; }

  .wordmark {
    position: absolute; display: flex; align-items: center;
    color: var(--logo-silver); font-weight: 400;
    text-transform: uppercase;
  }
  .wordmark__square { background: var(--logo-silver); border-radius: 4px; flex: none; }
  .wordmark__name { line-height: 1; white-space: nowrap; }
  .wordmark__name span { display: block; }

  .card--front .wordmark { top: 38px; left: 50%; transform: translateX(-50%); gap: 12px; }
  .card--front .wordmark__square { width: 44px; height: 52px; }
  .card--front .wordmark__name span:first-child { font-size: 36px; letter-spacing: 1px; }
  .card--front .wordmark__name span:last-child { font-size: 13px; letter-spacing: 3px; margin-top: 2px; }

  .contact-band {
    position: absolute; left: 0; top: 132px; width: 100%; height: 98px;
    background: linear-gradient(90deg, var(--silver-light) 0%, var(--silver-mid) 55%, var(--silver-dark) 100%);
    display: flex; align-items: center; color: var(--ink);
  }
  .contact-band__address {
    width: 250px; text-align: right; padding-right: 12px;
    font-size: 14.5px; line-height: 1.45;
  }
  .contact-band__divider { width: 1px; height: 62px; background: var(--ink); }
  .contact-band__lines { padding-left: 12px; font-size: 16px; line-height: 1.35; list-style: none; white-space: nowrap; }
  .contact-band__lines li { display: flex; align-items: center; gap: 5px; }
  .contact-band__lines li:last-child { font-size: 14px; }
  .contact-band__lines svg { width: 12px; height: 12px; flex: none; }

  .holder {
    position: absolute; left: 0; width: 100%; top: 246px;
    text-align: center; color: var(--white); font-size: 17px;
  }
  .holder strong { font-weight: 700; }

  .card--back .wordmark { top: 50%; left: 50%; transform: translate(-50%, -50%); gap: 18px; }
  .card--back .wordmark__square { width: 74px; height: 88px; }
  .card--back .wordmark__name span:first-child { font-size: 60px; letter-spacing: 2px; }
  .card--back .wordmark__name span:last-child { font-size: 21px; letter-spacing: 5px; margin-top: 4px; }
</style>
</head>
<body>
<main class="stage">
  <section class="card card--front" aria-label="Business card front">
    <div class="wordmark">
      <div class="wordmark__square"></div>
      <div class="wordmark__name"><span>Halden</span><span>Real Estate</span></div>
    </div>
    <div class="contact-band">
      <p class="contact-band__address">Street Name, City Name<br>State ZipCode</p>
      <div class="contact-band__divider"></div>
      <ul class="contact-band__lines">
        <li>
          <svg viewBox="0 0 12 12" aria-hidden="true"><circle cx="6" cy="6" r="5.3" fill="none" stroke="currentColor" stroke-width="1.2"/><path d="M4 3.2l1.2 1.4-.6.8c.4.9 1 1.5 1.9 1.9l.8-.6 1.4 1.2-.7 1c-2.4-.3-4.3-2.2-4.6-4.6z" fill="currentColor"/></svg>
          555-204-3187
        </li>
        <li>
          <svg viewBox="0 0 12 12" aria-hidden="true"><rect x="3" y="1" width="6" height="4" fill="currentColor"/><rect x="1" y="5" width="10" height="6" rx="1" fill="currentColor"/></svg>
          555-471-9062
        </li>
        <li>
          <svg viewBox="0 0 12 12" aria-hidden="true"><rect x="1" y="3" width="10" height="7" rx="1" fill="currentColor"/><path d="M1.5 3.5L6 7l4.5-3.5" fill="none" stroke="#ddd" stroke-width="1"/></svg>
          haldenrealestate@mail.com
        </li>
      </ul>
    </div>
    <p class="holder"><strong>Your Name,</strong> Title</p>
  </section>

  <section class="card card--back" aria-label="Business card back">
    <div class="wordmark">
      <div class="wordmark__square"></div>
      <div class="wordmark__name"><span>Halden</span><span>Real Estate</span></div>
    </div>
  </section>
</main>
</body>
</html>
```